Business Card Design Can you design a business card design? Looking for something unique and differe

Can you design a business card design? Looking for something unique and different. Can you design a business card design? Looking for something unique and different.Can you design a business card design? Looking for something unique and different.Can you design a business card design? Looking for something unique and different.Can you design a business card design? Looking for something unique and different.Can you design a business card design? Looking for something unique and different.

Industry/Entity Type

Business

Contact Information for Business Card

Can you design a business card design? Looking for something unique and different.

Font styles to use
Serif

```html
<!DOCTYPE html>
<html lang="en">
<head>
<meta charset="utf-8">
<title>Dosewise Business Card</title>
<link rel="stylesheet" href="https://fonts.googleapis.com/css2?family=Ubuntu:wght@500&family=Open+Sans:wght@400;600&display=swap">
<style>
  :root {
    --backdrop: #e6e6e6;
    --card-black: #0f0f10;
    --card-black-soft: #242426;
    --brand-purple: #9677a6;
    --swoosh-grey: #a4a4a4;
    --text-white: #f4f4f4;
    --card-shadow: rgba(0, 0, 0, 0.35);
  }
  * { margin: 0; padding: 0; box-sizing: border-box; }
  html, body { width: 1200px; height: 852px; overflow: hidden; }
  body {
    background: var(--backdrop);
    position: relative;
    font-family: "Open Sans", Arial, sans-serif;
  }
  .card {
    position: absolute;
    width: 520px;
    height: 300px;
    border-radius: 14px;
    overflow: hidden;
    background: linear-gradient(135deg, var(--card-black-soft) 0%, var(--card-black) 55%);
    box-shadow: 0 10px 24px var(--card-shadow);
  }
  .card--front { left: 70px; top: 140px; }
  .card--back { left: 610px; top: 410px; }

  .wordmark {
    font-family: "Ubuntu", Arial, sans-serif;
    font-weight: 500;
    color: var(--brand-purple);
    display: flex;
    align-items: center;
    gap: 12px;
    white-space: nowrap;
  }
  .wordmark__square {
    width: 0.7em;
    height: 0.7em;
    background: var(--brand-purple);
  }
  .card--front .wordmark {
    position: absolute;
    left: 0; right: 0; top: 118px;
    justify-content: center;
    font-size: 52px;
  }
  .card--back .wordmark {
    position: absolute;
    left: 34px; top: 34px;
    font-size: 40px;
  }

  .back-art { position: absolute; inset: 0; width: 100%; height: 100%; }

  .contact {
    position: absolute;
    left: 36px; top: 150px;
    color: var(--text-white);
    font-size: 12px;
    line-height: 1.6;
    white-space: nowrap;
  }
  .contact__address { margin-bottom: 8px; }
  .contact__list { list-style: none; }
  .contact__item { display: flex; align-items: center; gap: 9px; }
  .contact__icon { width: 12px; height: 12px; flex: none; }

  .holder {
    position: absolute;
    right: 22px; top: 190px;
    text-align: right;
    color: var(--text-white);
    white-space: nowrap;
  }
  .holder__name { font-family: "Ubuntu", Arial, sans-serif; font-weight: 500; font-size: 17px; }
  .holder__title { font-size: 10px; margin-top: 2px; }
</style>
</head>
<body>
  <section class="card card--front" aria-label="Card front">
    <div class="wordmark"><span class="wordmark__square"></span>Dosewise</div>
  </section>

  <section class="card card--back" aria-label="Card back">
    <svg class="back-art" viewBox="0 0 520 300" aria-hidden="true">
      <path fill="var(--swoosh-grey)" d="M0 264 C170 270 300 254 345 205 C390 155 430 72 500 40 C455 82 425 145 378 210 C330 268 190 282 0 278 Z"/>
      <path fill="var(--brand-purple)" d="M0 288 C160 292 300 280 358 222 C410 160 440 82 520 56 L520 300 L0 300 Z"/>
    </svg>

    <div class="wordmark"><span class="wordmark__square"></span>Dosewise</div>

    <div class="contact">
      <p class="contact__address">Your Commercial or office address with pincode</p>
      <ul class="contact__list">
        <li class="contact__item">
          <svg class="contact__icon" viewBox="0 0 12 12"><path fill="var(--brand-purple)" d="M1 3 Q6 0 11 3 L10 5 L8 4 L8 5 Q10 6 10 8 L10 11 L2 11 L2 8 Q2 6 4 5 L4 4 L2 5 Z"/></svg>
          <span>00.00.00.0000</span>
        </li>
        <li class="contact__item">
          <svg class="contact__icon" viewBox="0 0 12 12"><rect x="1" y="2.5" width="10" height="7" fill="var(--brand-purple)"/><path d="M1 2.5 L6 7 L11 2.5" fill="none" stroke="var(--card-black)" stroke-width="1"/></svg>
          <span>yourname@yourwebsite.com</span>
        </li>
        <li class="contact__item">
          <svg class="contact__icon" viewBox="0 0 12 12"><circle cx="6" cy="6" r="5" fill="var(--brand-purple)"/><path d="M1 6 H11 M6 1 V11" stroke="var(--card-black)" stroke-width="0.8"/></svg>
          <span>www.yourwebsite.com</span>
        </li>
      </ul>
    </div>

    <div class="holder">
      <p class="holder__name">Your Long Name</p>
      <p class="holder__title">Managing Director</p>
    </div>
  </section>
</body>
</html>
```